OBK Farcoast Logistics Limited

We need the buissnes card to be very exclusive. As we are all young in our company. We need this to be the gate to make our clients feel deep interest for us.

We are focused in as International Trade advisors, and our products go from Oil Tanker Ships to Rubber balls for dogs.

Our Slogan is Bringing Far Close.
And our main marketing will be through Internet.

We were stablished in 2009 In Mexico and we also have offices in Hong Kong.
We have representatives in China and Europe.

Target Market(s)

Is every company or Individual that wants to develop an International Project or product development or Logistic service of Goods and people.
Some of our current projects are Ship Brokerage, Mine Brokerage, Real State and Product Pormotional development.

Industry/Entity Type

It Company

Requirements
Must have
• Our Logo and slogan, and make the card accoriding to the logo.
Nice to have
• Our Colors

```html
<!DOCTYPE html>
<html lang="en">
<head>
<meta charset="utf-8">
<title>Business Card</title>
<link href="https://fonts.googleapis.com/css2?family=Open+Sans:wght@400;600;700&display=swap" rel="stylesheet">
<style>
  :root {
    --navy: #2b3990;
    --sky: #1b9ad6;
    --green: #8dc63f;
    --ink: #3a3a3a;
    --muted: #6d6e71;
    --paper: #ffffff;
    --backdrop: #eceae6;
    --divider: #d9d9d9;
  }
  * { margin: 0; padding: 0; box-sizing: border-box; }
  html, body {
    width: 1200px; height: 720px; overflow: hidden;
    background: var(--backdrop);
    font-family: "Open Sans", Arial, sans-serif;
  }
  .canvas {
    width: 1200px; height: 720px;
    display: flex; align-items: center; justify-content: center; gap: 40px;
  }
  .card {
    position: relative;
    width: 540px; height: 310px;
    background: var(--paper);
    box-shadow: 0 4px 14px rgba(0,0,0,0.12);
    overflow: hidden;
  }
  .card-front .band { position: absolute; inset: 0; }

  .brand { position: absolute; left: 40px; top: 70px; }
  .brand-mark { display: flex; align-items: center; gap: 10px; }
  .brand-dot { width: 34px; height: 34px; border-radius: 50%; background: var(--sky); }
  .brand-name { font-size: 44px; font-weight: 600; color: var(--green); letter-spacing: 2px; line-height: 1; }
  .brand-slogan { margin-top: 6px; font-size: 12px; color: var(--green); }

  .contact {
    position: absolute; left: 330px; top: 32px;
    padding-left: 14px;
    border-left: 1px solid var(--divider);
  }
  .contact-name { font-size: 18px; font-weight: 700; color: var(--navy); line-height: 1.1; }
  .contact-title { font-size: 11px; color: var(--muted); margin-bottom: 8px; }
  .contact-line { display: flex; align-items: center; gap: 6px; font-size: 13px; color: var(--ink); line-height: 1.6; }
  .contact-line svg { width: 11px; height: 11px; fill: var(--navy); flex: none; }

  .card-back { display: flex; flex-direction: column; align-items: center; justify-content: center; }
  .back-mark { display: flex; align-items: center; gap: 16px; margin-bottom: 26px; }
  .back-dot { width: 60px; height: 60px; border-radius: 50%; background: var(--sky); }
  .back-name { font-size: 72px; font-weight: 600; color: var(--green); letter-spacing: 4px; line-height: 1; }
  .back-slogan { font-size: 20px; color: var(--navy); }
  .back-web { font-size: 19px; color: var(--ink); letter-spacing: 3px; margin-top: 4px; }
</style>
</head>
<body>
<main class="canvas">

  <section class="card card-front" aria-label="Business card front">
    <svg class="band" viewBox="0 0 540 310" width="540" height="310">
      <path d="M0,262 L320,230 C338,228 344,214 362,212 L540,194 L540,222 L0,276 Z" fill="var(--navy)"/>
      <path d="M0,282 L540,228 L540,234 L0,288 Z" fill="var(--sky)"/>
      <text x="20" y="252" transform="rotate(-5.7 20 252)" font-family="Open Sans, Arial, sans-serif" font-size="13" fill="var(--ink)">Street Name, City Name, State Zip Code</text>
      <text x="378" y="222" transform="rotate(-5.7 378 222)" font-family="Open Sans, Arial, sans-serif" font-size="12.5" letter-spacing="1" fill="#ffffff">www.farcoast-obk.com</text>
    </svg>

    <div class="brand">
      <div class="brand-mark">
        <span class="brand-dot"></span>
        <span class="brand-name">OBK</span>
      </div>
      <p class="brand-slogan">Bringing Far Close</p>
    </div>

    <div class="contact">
      <p class="contact-name">Your Name</p>
      <p class="contact-title">Title</p>
      <p class="contact-line">
        <svg viewBox="0 0 24 24"><path d="M6.6 10.8a15 15 0 0 0 6.6 6.6l2.2-2.2a1 1 0 0 1 1-.25 11.4 11.4 0 0 0 3.6.57 1 1 0 0 1 1 1V20a1 1 0 0 1-1 1A17 17 0 0 1 3 4a1 1 0 0 1 1-1h3.5a1 1 0 0 1 1 1 11.4 11.4 0 0 0 .57 3.6 1 1 0 0 1-.25 1Z"/></svg>
        123-456-0789
      </p>
      <p class="contact-line">
        <svg viewBox="0 0 24 24"><path d="M7 1h10a2 2 0 0 1 2 2v18a2 2 0 0 1-2 2H7a2 2 0 0 1-2-2V3a2 2 0 0 1 2-2Zm0 3v14h10V4Zm5 15.5a1.2 1.2 0 1 0 0 2.4 1.2 1.2 0 0 0 0-2.4Z"/></svg>
        123-456-0789
      </p>
      <p class="contact-line">
        <svg viewBox="0 0 24 24"><path d="M2 5h20v14H2Zm2 2v.5l8 5 8-5V7Zm0 2.8V17h16V9.8l-8 5Z"/></svg>
        info@farcoast-obk.com
      </p>
    </div>
  </section>

  <section class="card card-back" aria-label="Business card back">
    <div class="back-mark">
      <span class="back-dot"></span>
      <span class="back-name">OBK</span>
    </div>
    <p class="back-slogan">Bringing Far Close</p>
    <p class="back-web">www.farcoast-obk.com</p>
  </section>

</main>
</body>
</html>
```